School Website

I need a design for a School (2 sections: Primary 6-12 years and Secondary 12-18 years). The first page is just a choice of the 2 sections. After we'll need 2 websites (with the same structure: Menu, ...) but with different colors. In fact, we need for end of October, 6 design of school website. So the best websites are going to be made available to you in the future (in pixelharbor) but privately.

Target Market(s)

Public, Parents, ...

Coding

Coded - Design and coding required

Number of Pages Required

5+ page

Font styles to use
Sans Serif

Colors
34a6d7
85cae6
cee9f5
ffffff

Requirements
Must have
• You can check the old Website: http: / /velmot.be We need the same pages with the same content. Menu: - HomePage - News and communication (like blog page) - Activities (like blog page, with photo gallery) - Contact (Contact form + maps) - In the main menu, we need a special button to connect to an external Website ( button needs to be different than the other menu items The name of this button is "Parents Area"). The logo of 2 sections are attached. Please use it for the design and the choice of colors.
Nice to have
• This is a web design of other school that we like: https://www.quintelo.be

```html
<!DOCTYPE html>
<html lang="en">
<head>
<meta charset="utf-8">
<title>Athénée Velmont – Kindergarten and Primary</title>
<link href="https://fonts.googleapis.com/css2?family=Fira+Sans:ital,wght@0,400;0,500;0,600;0,700;1,400&display=swap" rel="stylesheet">
<style>
:root{
  --blue:#34a6d7;
  --blue-deep:#1f8fd0;
  --blue-bar:#1466ad;
  --blue-light:#85cae6;
  --blue-pale:#cee9f5;
  --navy:#0e2a66;
  --ink:#2b2b2b;
  --muted:#6c6c6c;
  --grey-bg:#efefef;
  --dark:#151515;
  --white:#ffffff;
}
*{box-sizing:border-box;margin:0;padding:0}
html,body{width:1200px;height:4392px;overflow:hidden;background:var(--white)}
body{font-family:"Fira Sans",sans-serif;color:var(--ink)}
.page{position:relative;width:1200px;height:4392px;overflow:hidden}
.abs{position:absolute}
svg.ico{display:inline-block;vertical-align:middle}

/* top bar */
.topbar{left:0;top:0;width:1200px;height:41px;background:var(--blue-bar);color:var(--white);font-size:15px;font-weight:500}
.topbar .info{position:absolute;top:11px;display:flex;align-items:center;gap:7px}
.topbar .socials{position:absolute;right:50px;top:9px;display:flex;gap:8px}
.topbar .socials span{width:22px;height:22px;border:2px solid var(--white);border-radius:50%}

/* header */
.header{left:0;top:41px;width:1200px;height:90px;background:var(--white)}
.brand{position:absolute;left:52px;top:13px;display:flex;align-items:center;gap:10px}
.brand .dot{width:50px;height:50px;border-radius:50%;background:var(--blue-bar)}
.brand b{font-size:24px;font-weight:700;color:var(--blue-bar)}
.nav{position:absolute;left:494px;top:35px;display:flex;gap:36px;font-size:15px;font-weight:600;color:#333}
.parents{position:absolute;left:1009px;top:27px;width:145px;height:38px;border-radius:20px;background:var(--navy);color:var(--white);font-size:16px;font-weight:600;display:flex;align-items:center;justify-content:center;box-shadow:0 0 0 3px #c9d8ef}

/* hero */
.hero{left:0;top:131px;width:1200px;height:470px;overflow:hidden}
.hero .photo{position:absolute;inset:0;background:linear-gradient(90deg,#2f4f62 0%,#4c7a8a 35%,#7c9fa8 60%,#9db6c4 100%)}
.hero h1{position:absolute;left:48px;top:66px;color:var(--white);font-size:50px;font-weight:500;line-height:64px;letter-spacing:.5px}
.hero .sub{position:absolute;left:48px;top:184px;color:var(--white);font-size:24px;font-weight:500}
.hero .call{position:absolute;left:48px;top:261px;width:187px;height:51px;border-radius:26px;background:#000;color:var(--white);font-size:19px;font-weight:500;display:flex;align-items:center;justify-content:center;gap:8px}
.hero svg.wave{position:absolute;left:0;top:330px}
.dots{display:flex;gap:24px;align-items:center}
.dots i{display:block;width:10px;height:10px;border-radius:50%;background:var(--blue-deep)}
.dots i.on{width:16px;height:16px;background:var(--white);border:3px solid var(--blue-deep);box-shadow:inset 0 0 0 2px var(--white);background-clip:padding-box}
.hero .dots i{background:var(--white)}
.hero .dots i.on{border-color:#8bc53f;background:var(--white)}

/* feature cards */
.card{background:var(--white);box-shadow:0 2px 10px rgba(0,0,0,.18);text-align:center}
.card h3{position:absolute;left:0;right:0;top:145px;font-size:19px;font-weight:600;color:var(--blue-deep)}
.btn-more{position:absolute;height:38px;border-radius:20px;background:var(--white);box-shadow:0 1px 7px rgba(0,0,0,.28);font-size:15px;color:#222;display:flex;align-items:center;justify-content:center;gap:6px}

/* info band */
.band{left:48px;top:963px;width:1103px;height:106px;background:linear-gradient(90deg,#3d5b2f 0%,#5d7d3a 40%,#6f8f45 70%,#8aa15a 100%)}
.band h2{position:absolute;left:24px;top:36px;color:var(--white);font-size:30px;font-weight:600}
.band .call{position:absolute;right:52px;top:27px;width:175px;height:50px;border-radius:26px;background:var(--white);font-size:20px;font-weight:600;color:#222;display:flex;align-items:center;justify-content:center;gap:10px}

/* news */
.news{left:0;top:1125px;width:1200px;height:668px;background:var(--grey-bg)}
.sec-title{font-size:29px;font-weight:600;color:#262626;letter-spacing:.3px}
.arrows{position:absolute;right:55px;top:54px;display:flex;gap:10px}
.arrows span{width:32px;height:24px;background:#111;display:flex;align-items:center;justify-content:center}
.post{position:absolute;top:125px;width:340px}
.post .img{height:243px;border:3px solid var(--white);box-shadow:0 1px 4px rgba(0,0,0,.15)}
.post h4{margin-top:34px;font-size:19px;font-weight:600;color:var(--blue-deep)}
.post .meta{margin-top:12px;padding:10px 0 6px;border-top:1px solid #d8d8d8;display:flex;justify-content:space-between;font-size:12px;font-weight:500;color:#555;text-transform:uppercase}
.post .meta span{display:flex;align-items:center;gap:8px}
.post p{margin-top:12px;font-size:13px;line-height:21px;color:#666}

/* team */
.team{left:48px;top:1846px;width:1101px;height:544px;background:var(--white);box-shadow:0 2px 10px rgba(0,0,0,.15)}
.member{position:absolute;top:130px;width:230px;text-align:center}
.member .ring{width:170px;height:170px;margin:0 auto;border-radius:50%;box-shadow:-4px 5px 0 var(--blue-deep),4px 7px 0 #000}
.member .face{width:170px;height:170px;border-radius:50%;background:radial-gradient(circle at 50% 40%,#d8c2b0 0%,#b39a87 45%,#e6e6e6 46%,#f1f1f1 100%)}
.member h4{margin-top:22px;font-size:20px;font-weight:600;color:var(--blue-deep)}
.member em{display:block;margin-top:6px;font-size:14px;color:#777}
.member p{margin-top:8px;font-size:14px;font-weight:500;color:#555}

/* contacts */
.contacts{left:49px;top:2441px;width:340px;height:498px;background:var(--white);box-shadow:0 2px 10px rgba(0,0,0,.15)}
.contacts h2{position:absolute;left:39px;top:44px}
.contacts .inner{position:absolute;left:40px;top:107px;width:260px;height:363px;box-shadow:0 1px 8px rgba(0,0,0,.15)}
.person{position:absolute;left:26px;width:210px;padding-bottom:14px;border-bottom:1px solid #d2d2d2}
.person b{display:block;font-size:15px;font-weight:600;color:var(--blue-deep)}
.person em{display:block;margin-top:8px;font-size:14px;color:#777}
.person span{display:flex;align-items:center;gap:12px;margin-top:10px;font-size:13px;color:#555}

/* activities */
.acts{left:441px;top:2514px;width:699px;height:428px;background:var(--white);box-shadow:0 2px 10px rgba(0,0,0,.15)}
.event{position:absolute;left:57px;width:586px;height:160px;background:var(--white);box-shadow:0 1px 8px rgba(0,0,0,.16)}
.event .img{position:absolute;left:0;top:0;width:242px;height:160px}
.event .date{position:absolute;left:0;top:0;width:58px;height:96px;background:#000;color:var(--white);text-align:center;font-weight:600;padding-top:22px;font-size:19px;line-height:32px}
.event h4{position:absolute;left:262px;top:24px;font-size:20px;font-weight:500;color:#222}
.event .row{position:absolute;left:262px;display:flex;align-items:center;gap:16px;font-size:13px;color:#555}

/* gallery */
.gallery{left:0;top:2983px;width:1200px;height:680px}
.gallery h2{position:absolute;left:0;right:0;top:48px;text-align:center;color:var(--white)}
.shot{position:absolute;width:252px;height:196px;box-shadow:0 2px 8px rgba(0,0,0,.45)}

/* contact */
.contact{left:0;top:3724px;width:1200px;height:575px}
.contact h2{position:absolute;left:600px;width:550px;top:168px;text-align:center;color:var(--white);font-size:31px}
.field{position:absolute;background:var(--white);border-radius:10px;font-size:14px;font-style:italic;color:#888;padding:12px 18px}
.submit{position:absolute;left:796px;top:432px;width:159px;height:52px;border-radius:26px;background:var(--blue-deep);color:var(--white);font-size:20px;font-weight:600;display:flex;align-items:center;justify-content:center;gap:8px}

/* footer */
.footer{left:0;top:4299px;width:1200px;height:93px;background:#101a33;color:#c9c9c9;font-size:15px}
.footer .copy{position:absolute;left:50px;top:46px}
.footer .socials{position:absolute;right:50px;top:30px;display:flex;gap:16px}
.footer .socials span{width:40px;height:40px;border-radius:50%;border:3px solid var(--white)}
</style>
</head>
<body>
<svg width="0" height="0" style="position:absolute">
  <defs>
    <symbol id="i-phone" viewBox="0 0 24 24"><path d="M6.6 10.8a15.1 15.1 0 0 0 6.6 6.6l2.2-2.2a1 1 0 0 1 1-.25 11.4 11.4 0 0 0 3.6.57 1 1 0 0 1 1 1V20a1 1 0 0 1-1 1A17 17 0 0 1 3 4a1 1 0 0 1 1-1h3.5a1 1 0 0 1 1 1c0 1.25.2 2.45.57 3.57a1 1 0 0 1-.25 1z" fill="currentColor"/></symbol>
    <symbol id="i-pin" viewBox="0 0 24 24"><path d="M12 2a7 7 0 0 0-7 7c0 5.2 7 13 7 13s7-7.8 7-13a7 7 0 0 0-7-7zm0 9.5A2.5 2.5 0 1 1 12 6.5a2.5 2.5 0 0 1 0 5z" fill="currentColor"/></symbol>
    <symbol id="i-clock" viewBox="0 0 24 24"><circle cx="12" cy="12" r="9" fill="none" stroke="currentColor" stroke-width="2.4"/><path d="M12 7v5h4" fill="none" stroke="currentColor" stroke-width="2.4" stroke-linecap="round"/></symbol>
    <symbol id="i-arrow" viewBox="0 0 24 24"><path d="M4 12h14M13 6l6 6-6 6" fill="none" stroke="currentColor" stroke-width="3" stroke-linecap="round" stroke-linejoin="round"/></symbol>
    <symbol id="i-cal" viewBox="0 0 24 24"><rect x="3" y="5" width="18" height="16" rx="1" fill="none" stroke="currentColor" stroke-width="2"/><path d="M3 10h18M8 3v4M16 3v4" stroke="currentColor" stroke-width="2"/><path d="M7 13h2v2H7zM11 13h2v2h-2zM15 13h2v2h-2zM7 17h2v2H7zM11 17h2v2h-2z" fill="currentColor"/></symbol>
    <symbol id="i-chat" viewBox="0 0 24 24"><path d="M3 5h12v8H8l-4 3v-3H3z" fill="currentColor"/><path d="M17 8h4v8h-1v3l-3-3h-6v-2h6z" fill="#8bc53f"/></symbol>
    <symbol id="i-send" viewBox="0 0 24 24"><path d="M2 11 22 3l-6 18-4-7z" fill="currentColor"/></symbol>
  </defs>
</svg>

<div class="page">

  <!-- top bar -->
  <div class="abs topbar">
    <div class="info" style="left:48px"><svg class="ico" width="16" height="16"><use href="#i-phone"/></svg>+32 10 44 71 58</div>
    <div class="info" style="left:197px"><svg class="ico" width="18" height="18"><use href="#i-pin"/></svg>Rue des Tilleuls , Belgium</div>
    <div class="info" style="left:414px"><svg class="ico" width="18" height="18"><use href="#i-clock"/></svg>Mon- Fri 7 am - 6 pm</div>
    <div class="socials" aria-label="Social links"><span></span><span></span><span></span></div>
  </div>

  <!-- header -->
  <div class="abs header">
    <div class="brand"><span class="dot"></span><b>Athénée Velmont</b></div>
    <nav class="nav"><span>Home</span><span>News</span><span>Activities</span><span>Gallery</span><span>Contact</span></nav>
    <div class="parents">Parents Area</div>
  </div>

  <!-- hero -->
  <section class="abs hero">
    <div class="photo" role="img" aria-label="Smiling schoolboy in front of a colourful painted wall"></div>
    <h1>WELCOME TO<br>Athenee Velmont</h1>
    <div class="sub">Kindergarten and Primary</div>
    <div class="call"><svg class="ico" width="18" height="18"><use href="#i-phone"/></svg>Call Us</div>
    <svg class="wave" width="1200" height="140" viewBox="0 0 1200 140">
      <path d="M0,60 C250,100 480,125 620,128 C850,133 1050,90 1200,40 L1200,140 L0,140 Z" fill="#fff"/>
      <path d="M0,15 C240,100 480,126 640,128 C480,124 240,98 0,62 Z" fill="#1466ad"/>
      <path d="M1200,0 C1030,80 820,126 560,132 C840,138 1060,92 1200,44 Z" fill="#000"/>
    </svg>
    <div class="dots abs" style="left:535px;top:398px"><i class="on"></i><i></i><i></i><i></i></div>
  </section>

  <!-- feature cards -->
  <div class="abs card" style="left:66px;top:648px;width:510px;height:260px">
    <svg class="abs" style="left:204px;top:26px" width="102" height="102" viewBox="0 0 100 100"><circle cx="50" cy="50" r="42" fill="none" stroke="#8bc53f" stroke-width="10"/><circle cx="50" cy="50" r="42" fill="none" stroke="#1f8fd0" stroke-width="10" stroke-dasharray="66 300" transform="rotate(0 50 50)"/><path d="M50 22v28h22" fill="none" stroke="#1f8fd0" stroke-width="8" stroke-linecap="round"/></svg>
    <h3>OUR SCHEDULES AND DAYCARE</h3>
    <div class="btn-more" style="left:189px;top:195px;width:137px">Know More <svg class="ico" width="16" height="16" style="color:#1f8fd0"><use href="#i-arrow"/></svg></div>
  </div>
  <div class="abs card" style="left:619px;top:648px;width:510px;height:260px">
    <svg class="abs" style="left:206px;top:26px" width="100" height="100" viewBox="0 0 100 100"><path d="M20 34 Q40 8 72 22 Z" fill="#8bc53f"/><path d="M44 20 L58 80" stroke="#1f8fd0" stroke-width="5"/><path d="M10 64 L34 84 M14 74 L54 70 L70 88" fill="none" stroke="#1f8fd0" stroke-width="5" stroke-linecap="round"/></svg>
    <h3>SCHOOL HOLIDAYS</h3>
    <div class="btn-more" style="left:187px;top:195px;width:137px">Know More <svg class="ico" width="16" height="16" style="color:#1f8fd0"><use href="#i-arrow"/></svg></div>
  </div>

  <!-- info band -->
  <div class="abs band" role="img" aria-label="Grass field with stacked school books">
    <h2>More Information</h2>
    <div class="call"><svg class="ico" width="24" height="24" style="color:#1f8fd0"><use href="#i-phone"/></svg>Call Us</div>
  </div>

  <!-- latest news -->
  <section class="abs news">
    <h2 class="sec-title abs" style="left:47px;top:48px">LATEST NEWS</h2>
    <div class="arrows"><span><svg width="14" height="14" viewBox="0 0 24 24"><path d="M15 5l-7 7 7 7" fill="none" stroke="#fff" stroke-width="3"/></svg></span><span><svg width="14" height="14" viewBox="0 0 24 24"><path d="M9 5l7 7-7 7" fill="none" stroke="#fff" stroke-width="3"/></svg></span></div>

    <article class="post" style="left:48px">
      <div class="img" role="img" aria-label="Group of cheering children in front of a cartoon school" style="background:linear-gradient(180deg,#9fd3ef 0%,#d9c36a 50%,#e0563d 100%)"></div>
      <h4>Loreum Ipsum Dummy Text</h4>
      <div class="meta"><span><svg width="18" height="18" style="color:#8bc53f"><use href="#i-cal"/></svg>Auguest 23,2019</span><span><svg width="22" height="18" style="color:#1f8fd0"><use href="#i-chat"/></svg>No comments</span></div>
      <p>Great progress is developing at the Conco B Loreum tex ! More documentation will come as this project pulls together.</p>
    </article>
    <article class="post" style="left:424px">
      <div class="img" role="img" aria-label="Schoolgirl giving a thumbs up in front of a chalkboard" style="background:linear-gradient(135deg,#4f8a4c 0%,#d6a36a 45%,#ee6aa6 75%,#f1f1f1 100%)"></div>
      <h4>Loreum Ipsum Dummy Text</h4>
      <div class="meta"><span><svg width="18" height="18" style="color:#8bc53f"><use href="#i-cal"/></svg>Auguest 23,2019</span><span><svg width="22" height="18" style="color:#1f8fd0"><use href="#i-chat"/></svg>No comments</span></div>
      <p>Great progress is developing at the Conco B Loreum tex ! More documentation will come as this project pulls together.</p>
    </article>
    <article class="post" style="left:801px">
      <div class="img" role="img" aria-label="Child in an aviator hat holding a toy plane beside coloured pencils" style="background:linear-gradient(180deg,#ffffff 0%,#f3e3c2 55%,#e3a546 80%,#d94c3a 100%)"></div>
      <h4>Loreum Ipsum Dummy Text</h4>
      <div class="meta"><span><svg width="18" height="18" style="color:#8bc53f"><use href="#i-cal"/></svg>Auguest 23,2019</span><span><svg width="22" height="18" style="color:#1f8fd0"><use href="#i-chat"/></svg>No comments</span></div>
      <p>Great progress is developing at the Conco B Loreum tex ! More documentation will come as this project pulls together.</p>
    </article>
    <div class="btn-more" style="left:43px;top:574px;width:136px">Know More <svg class="ico" width="16" height="16" style="color:#1f8fd0"><use href="#i-arrow"/></svg></div>
    <div class="btn-more" style="left:420px;top:574px;width:136px">Know More <svg class="ico" width="16" height="16" style="color:#1f8fd0"><use href="#i-arrow"/></svg></div>
    <div class="btn-more" style="left:797px;top:574px;width:136px">Know More <svg class="ico" width="16" height="16" style="color:#1f8fd0"><use href="#i-arrow"/></svg></div>
  </section>

  <!-- teaching team -->
  <section class="abs team">
    <h2 class="sec-title" style="position:absolute;left:0;right:0;top:46px;text-align:center">OUR TEACHING TEAM</h2>
    <div class="member" style="left:37px"><div class="ring"><div class="face" role="img" aria-label="Portrait of a teacher"></div></div><h4>LUCIE MARCHAL</h4><em>Kindergarten section</em><p>Holder of the class of M1</p></div>
    <div class="member" style="left:304px"><div class="ring"><div class="face" role="img" aria-label="Portrait of a teacher"></div></div><h4>LUCIE MARCHAL</h4><em>Kindergarten section</em><p>Holder of the class of M1</p></div>
    <div class="member" style="left:575px"><div class="ring"><div class="face" role="img" aria-label="Portrait of a teacher"></div></div><h4>LUCIE MARCHAL</h4><em>Kindergarten section</em><p>Holder of the class of M1</p></div>
    <div class="member" style="left:844px"><div class="ring"><div class="face" role="img" aria-label="Portrait of a teacher"></div></div><h4>LUCIE MARCHAL</h4><em>Kindergarten section</em><p>Holder of the class of M1</p></div>
    <div class="dots abs" style="left:492px;top:474px"><i class="on"></i><i></i><i></i><i></i></div>
  </section>

  <!-- useful contacts -->
  <section class="abs contacts">
    <h2 class="sec-title">USEFUL CONTACTS</h2>
    <div class="inner">
      <div class="person" style="top:26px"><b>MRS HÉLÈNE DORVAL</b><em>Prefect of studies</em><span><svg width="22" height="22" style="color:#1f8fd0"><use href="#i-phone"/></svg>010 -00-0058</span></div>
      <div class="person" style="top:150px"><b>MRS CLAIRE VANDAMME</b><em>Secretariat</em><span><svg width="22" height="22" style="color:#1f8fd0"><use href="#i-phone"/></svg>010 -00-0058</span></div>
      <div class="btn-more" style="left:51px;top:275px;width:136px">View All <svg class="ico" width="16" height="16" style="color:#1f8fd0"><use href="#i-arrow"/></svg></div>
    </div>
  </section>

  <!-- activities -->
  <h2 class="sec-title abs" style="left:440px;top:2437px">ACTIVITIES</h2>
  <section class="abs acts">
    <div class="event" style="top:31px">
      <div class="img" role="img" aria-label="Sports hall with a wooden roof" style="background:linear-gradient(180deg,#a0683a 0%,#c9ccd2 45%,#8a8f98 100%)"></div>
      <div class="date">SEPT<br>20</div>
      <h4>Loreum ipsum dummy text</h4>
      <div class="row" style="top:70px"><svg width="24" height="24" style="color:#1f8fd0"><use href="#i-clock"/></svg>12:00 p.m - 5:00 p.m</div>
      <div class="row" style="top:112px"><svg width="24" height="26" style="color:#1f8fd0"><use href="#i-pin"/></svg>Loreum ipsum dummy text ,14th Etd.</div>
    </div>
    <div class="event" style="top:208px">
      <div class="img" role="img" aria-label="Children in beekeeping suits on an outing" style="background:linear-gradient(180deg,#6d8a5a 0%,#d8dde3 45%,#9aa1ab 100%)"></div>
      <div class="date">SEPT<br>20</div>
      <h4>Loreum ipsum dummy text</h4>
      <div class="row" style="top:70px"><svg width="24" height="24" style="color:#1f8fd0"><use href="#i-clock"/></svg>12:00 p.m - 5:00 p.m</div>
      <div class="row" style="top:112px"><svg width="24" height="26" style="color:#1f8fd0"><use href="#i-pin"/></svg>Loreum ipsum dummy text ,14th Etd.</div>
    </div>
    <div class="dots abs" style="left:300px;top:396px"><i class="on"></i><i></i><i></i><i></i></div>
  </section>

  <!-- gallery -->
  <section class="abs gallery">
    <svg class="abs" style="left:0;top:0" width="1200" height="680" viewBox="0 0 1200 680">
      <path d="M0,190 Q600,-70 1200,190 L1200,500 Q600,790 0,500 Z" fill="#262a30"/>
      <path d="M0,190 Q600,-70 1200,190 L1200,500 Q600,790 0,500 Z" fill="#3a4452" opacity=".5" role="img" aria-label="School building at dusk"/>
      <path d="M600,56 Q950,62 1200,190 L1200,214 Q950,84 600,60 Z" fill="#1466ad"/>
      <path d="M0,190 Q250,62 600,56 L600,60 Q250,82 0,214 Z" fill="#000"/>
      <path d="M0,500 Q250,620 600,665 L600,660 Q250,600 0,476 Z" fill="#1466ad"/>
      <path d="M1200,500 Q950,620 600,665 L600,660 Q950,600 1200,476 Z" fill="#000"/>
    </svg>
    <h2 class="sec-title">GALLERY</h2>
    <div class="shot" role="img" aria-label="Children playing with stacking toys" style="left:51px;top:230px;background:linear-gradient(135deg,#e9c49c,#c98e62 50%,#e5e5e5)"></div>
    <div class="shot" role="img" aria-label="Teacher with children at a craft table" style="left:329px;top:128px;background:linear-gradient(135deg,#f1ede8,#d99a7e 50%,#b23a3a)"></div>
    <div class="shot" role="img" aria-label="Child crawling on a classroom floor" style="left:329px;top:344px;background:linear-gradient(135deg,#e7dccb,#c9a88c 50%,#8e7a6a)"></div>
    <div class="shot" role="img" aria-label="Children drawing in a bright classroom" style="left:617px;top:128px;background:linear-gradient(135deg,#eef1f3,#e8c46a 50%,#d9553a)"></div>
    <div class="shot" role="img" aria-label="Boys using a tablet at a desk" style="left:617px;top:344px;background:linear-gradient(135deg,#a9c3de,#4d79b2 50%,#d7b28a)"></div>
    <div class="shot" role="img" aria-label="Pupils reading together at a table" style="left:898px;top:230px;background:linear-gradient(135deg,#f0ede6,#d6b08a 50%,#6aa2d2)"></div>
    <div class="dots abs" style="left:545px;top:588px"><i class="on"></i><i></i><i></i><i></i></div>
  </section>

  <!-- contact -->
  <section class="abs contact">
    <svg class="abs" style="left:0;top:0" width="1200" height="575" viewBox="0 0 1200 575">
      <defs><clipPath id="arc"><path d="M0,200 Q600,-60 1200,200 L1200,575 L0,575 Z"/></clipPath></defs>
      <g clip-path="url(#arc)">
        <rect x="0" y="0" width="1200" height="575" fill="#4a4046" role="img" aria-label="School building facade"/>
        <rect x="600" y="0" width="600" height="575" fill="#0d0d0d"/>
        <rect x="68" y="0" width="532" height="575" fill="#dfe7d8" role="img" aria-label="Map of Belgium with the school location"/>
      </g>
      <path d="M0,200 Q600,-60 1200,200 L1200,226 Q600,-40 0,226 Z" fill="#000"/>
      <path d="M0,200 Q300,70 600,66 L600,72 Q300,84 0,216 Z" fill="#1466ad"/>
      <path d="M418,218 a14 14 0 1 1 0.1 0 M418,218 l0,0" fill="none"/>
      <path d="M418 186a16 16 0 0 0-16 16c0 12 16 30 16 30s16-18 16-30a16 16 0 0 0-16-16z" fill="#e03a3a"/>
      <circle cx="418" cy="202" r="6" fill="#fff"/>
    </svg>
    <h2 class="sec-title">CONTACT US</h2>
    <div class="field" style="left:656px;top:244px;width:198px;height:41px">Name</div>
    <div class="field" style="left:895px;top:244px;width:198px;height:41px">Email</div>
    <div class="field" style="left:656px;top:316px;width:435px;height:77px">Message</div>
    <div class="submit"><svg width="18" height="18" style="color:#fff"><use href="#i-send"/></svg>Submit</div>
  </section>

  <!-- footer -->
  <footer class="abs footer">
    <div class="copy">© 2019 Copyrights @ Athenee Velmont All Rights Reserved</div>
    <div class="socials" aria-label="Social links"><span></span><span></span><span></span><span></span></div>
  </footer>

</div>
</body>
</html>
```